Broschüre
Zielgruppe
Die T.O.R.K. Lumen Holding GmbH ist ein inhabergeführtes Immobilienunternehmen mit Sitz in Moers. Wir sind spezialisiert auf den direkten Ankauf von Mehrfamilienhäusern, Wohnanlagen und größeren Wohnimmobilien in Nordrhein-Westfalen. Unser Schwerpunkt liegt auf einer schnellen, diskreten und unbürokratischen Abwicklung – vom ersten Kontakt bis zum notariellen Abschluss. Wir kaufen Objekte in jedem Zustand, ob vermietet, leerstehend oder sanierungsbedürftig.
Wer ist Deine Zielgruppe?
• Institutionelle Eigentümer z.b. Wohnungsunternehmen und Investoren, die Bestände veräußern wollen
Aufgabenstellung
• Corporate Identity: Seriös, modern, vertrauenswürdig. Die Broschüre soll unsere Professionalität und Diskretion betonen.
• Farben: Anlehnung an die Unternehmensfarben der T.O.R.K. Lumen Holding GmbH (dezent, elegant, z. B. dunkles Blau, Grau, Weiß; ggf. Akzentfarbe Gold oder ein warmes Gelb).
• Schriftarten: Gut lesbar, modern, ohne verschnörkelte Fonts.
• Format: Hochformat DIN A4, 4–8 Seiten, übersichtlich und klar strukturiert.
• Bildsprache: Hochwertige Immobilienbilder, urbane Aufnahmen aus NRW, Detailfotos (z. B. Architektur, Gebäudeansichten) sowie emotionale Motive, die Vertrauen und Sicherheit vermitteln.
• Ton & Stil: Seriös, diskret, aber sympathisch – nicht zu werblich, sondern lösungsorientiert.
• Logo: Unser Firmenlogo muss auf dem Titel und der Rückseite gut sichtbar platziert sein.

```html
<!DOCTYPE html>
<html lang="de">
<head>
<meta charset="utf-8">
<title>Broschüre – Unser Fokus</title>
<link href="https://fonts.googleapis.com/css2?family=Cormorant+Garamond:wght@400;500&family=Libre+Caslon+Text:wght@700&family=Montserrat:wght@400;700&display=swap" rel="stylesheet">
<style>
  :root {
    --navy: #2e3468;
    --navy-deep: #1c2048;
    --gold: #dcbb55;
    --gold-line: #b89a52;
    --white: #ffffff;
    --backdrop: #dcdcdf;
    --photo-warm: #b0704a;
    --photo-dark: #3a3a36;
  }
  * { margin: 0; padding: 0; box-sizing: border-box; }
  html, body { width: 1200px; height: 1200px; overflow: hidden; background: var(--backdrop); }
  .spread {
    position: absolute; left: 40px; top: 204px;
    width: 1120px; height: 792px; display: flex;
    box-shadow: 0 10px 40px rgba(0,0,0,0.18);
  }
  .page { position: relative; width: 560px; height: 792px; color: var(--white); }
  .page--left { background: linear-gradient(90deg, var(--navy) 0%, var(--navy) 80%, var(--navy-deep) 100%); }
  .page--right { background: linear-gradient(90deg, var(--navy-deep) 0%, var(--navy) 8%, var(--navy-deep) 30%, var(--navy-deep) 100%); }

  .section-label {
    position: absolute; top: 44px;
    font-family: "Cormorant Garamond", serif; font-size: 13px; letter-spacing: 0.5px;
    padding-bottom: 7px; border-bottom: 1px solid var(--gold-line);
  }
  .page--left .section-label { left: 54px; padding-right: 36px; }
  .page--right .section-label { right: 40px; top: 150px; padding-left: 30px; }

  .headline {
    position: absolute; left: 54px; top: 150px;
    font-family: "Libre Caslon Text", serif; font-weight: 700;
    font-size: 34px; line-height: 1.08; letter-spacing: 2px;
    color: var(--gold); text-transform: uppercase;
  }
  .body-copy {
    position: absolute; left: 74px; top: 300px; width: 440px;
    font-family: "Montserrat", sans-serif; font-size: 13.5px;
    line-height: 1.42; letter-spacing: 0.6px;
  }
  .body-copy .rule {
    position: absolute; left: -26px; top: -6px; width: 1px; height: 66px; background: var(--gold-line);
  }
  .body-copy p { margin-bottom: 14px; }
  .body-copy .lead { padding-left: 24px; margin-bottom: 12px; }
  .body-copy .emphasis { font-weight: 700; letter-spacing: 0.4px; }

  .folio {
    position: absolute; bottom: 40px;
    font-family: "Montserrat", sans-serif; font-size: 11px; letter-spacing: 1.5px;
    padding-top: 9px; border-top: 1px solid var(--gold-line);
  }
  .folio strong { font-weight: 700; }
  .page--left .folio { left: 54px; padding-right: 50px; }
  .page--right .folio { right: 40px; padding-left: 50px; }

  .photo {
    position: absolute; left: 46px; top: 70px; width: 360px; height: 640px;
    background: linear-gradient(160deg, var(--photo-warm) 0%, #8b6a52 40%, var(--photo-dark) 100%);
  }
  .frame-rule {
    position: absolute; right: 44px; top: 200px; width: 1px; height: 500px; background: var(--gold-line);
  }
</style>
</head>
<body>
  <main class="spread">
    <section class="page page--left">
      <div class="section-label">Unser Fokus</div>
      <h1 class="headline">Wir investieren<br>in Werte<br>die bleiben.</h1>
      <div class="body-copy">
        <span class="rule"></span>
        <p class="lead">Unsere Schwerpunkte:</p>
        <p>Objekttyp: Mehrfamilienhäuser, Wohnanlagen, Wohnportfolios<br>
           Zustand: Auch teilvermietet, sanierungsbedürftig oder mit Leerstand<br>
           Volumen: Bis zu 10 Millionen Euro Investitionssumme pro Objekt</p>
        <p>Regionale Fokussierung:<br>
           Moers, Duisburg, Kamp-Lintfort, Neukirchen-Vluyn sowie angrenzende Städte im Ruhrgebiet und am Niederrhein</p>
        <p class="emphasis">Wir sehen Potenziale dort, wo andere nur Risiken sehen – sprechen Sie uns gerne auch bei Sonderfällen an.</p>
      </div>
      <div class="folio">Seite: <strong>03</strong></div>
    </section>
    <section class="page page--right">
      <div class="photo" role="img" aria-label="Luftaufnahme einer Wohnsiedlung mit roten Ziegeldächern, Straßen und Grünflächen"></div>
      <div class="section-label">Unser Fokus</div>
      <div class="frame-rule"></div>
      <div class="folio">Seite: <strong>04</strong></div>
    </section>
  </main>
</body>
</html>
```